Push notification screens at app start up

We have an existing news publication app platform and are adding categories to push notifications.

We need two screens designed (each for Zorbel, Quillet and Android for a total of 6d) that show when the app is first launched.

The workflow of our app:
0. app launch screen while webservices run (no work needed)
1. information screen to the user promoting the benefits of push notification with "Next" button. (see concept attached)
2. Push categories selection screen. This will have list of category types, with on/off switch.

"Select the categories that you wish to receive occasional notices:
Breaking News (on/off switch)
Local News (on/off switch)
Sports (on/off switch)
Local Events (on/off switch)
Weather Alerts (on/off switch)
Local Deals (on/off switch)"

"Enable these categories on the next screen."
"Next" button

Background:
When I was looking around at app designs, I came across this one (http://www.plinthworks.example/design/7719034) and I really liked it. We obviously have different features on our screen, but I’d like to have this same feel. The colors used in this design are perfect.

UPDATE: I do not mean to limit your design to match the layout as the one mentioned above. Please use your creativity for the layout.

Our standard font in Helvetica Neue.

Notes:
- our app is developed for all phone devices from Zorbel 4 to Zorbel 6, so designs should be thoughtful of vertical scrolling if needed.
- our app is developed for Quillets, so we'll need designs completed as well. (We can finalize Zorbel design first, then translate the design to Quillet.)
- our app is developed for Android phones (not tablets), so we'll need designs completed as well. (We can finalize iOS design first, then translater to Android UI design guidelines).

We hope to establish a good on-going relationship with the designer for as-needed work in the future.

News

• Helvetica Neue

• Clean designs. No clutter.
• We would likely go with the standard on/off switches for both iOS and Android, but are open to small custom variations.

```html
<!DOCTYPE html>
<html lang="en">
<head>
<meta charset="utf-8">
<title>Notifications – Onboarding</title>
<link rel="stylesheet" href="https://fonts.googleapis.com/css2?family=Arimo:wght@400;700&display=swap">
<style>
  :root {
    --brand-blue: #2b7ee3;
    --surface: #ffffff;
    --ink: #111111;
    --on-brand: #ffffff;
  }
  * { box-sizing: border-box; margin: 0; padding: 0; }
  html, body {
    width: 675px;
    height: 1200px;
    overflow: hidden;
    background: var(--surface);
    font-family: "Arimo", "Helvetica Neue", Helvetica, Arial, sans-serif;
  }
  .screen {
    position: relative;
    width: 675px;
    height: 1200px;
    background: var(--surface);
    overflow: hidden;
  }
  .header-shape {
    position: absolute;
    top: 0; left: 0;
    width: 675px;
    height: 330px;
  }
  .status-bar {
    position: absolute;
    top: 0; left: 0; right: 0;
    height: 50px;
    color: var(--on-brand);
    font-size: 22px;
  }
  .status-bar .carrier {
    position: absolute;
    left: 12px; top: 13px;
    display: flex; align-items: center; gap: 8px;
  }
  .status-bar .time {
    position: absolute;
    left: 0; right: 0; top: 13px;
    text-align: center;
    font-weight: 700;
  }
  .status-bar .system {
    position: absolute;
    right: 12px; top: 13px;
    display: flex; align-items: center; gap: 10px;
  }
  .screen-title {
    position: absolute;
    top: 84px; left: 0; right: 0;
    text-align: center;
    color: var(--on-brand);
    font-size: 38px;
    font-weight: 400;
  }
  .intro {
    position: absolute;
    top: 402px; left: 60px; right: 60px;
    text-align: center;
    color: var(--ink);
    font-size: 25px;
    line-height: 36px;
  }
  .intro p + p { margin-top: 36px; }
  .next-button {
    position: absolute;
    left: 0; right: 0; bottom: 0;
    height: 109px;
    background: var(--brand-blue);
    color: var(--on-brand);
    display: flex; align-items: center; justify-content: center; gap: 28px;
    font-size: 27px;
    font-weight: 700;
    letter-spacing: 1px;
  }
</style>
</head>
<body>
<main class="screen">
  <svg class="header-shape" viewBox="0 0 675 330" aria-hidden="true">
    <path d="M0 0 H675 V165 Q337.5 263 0 165 Z" fill="var(--brand-blue)"/>
    <circle cx="337.5" cy="241" r="74" fill="var(--brand-blue)" stroke="var(--surface)" stroke-width="6"/>
    <g class="megaphone-icon" fill="var(--on-brand)">
      <path d="M296 226 h16 l30 -18 v66 l-30 -18 h-16 z"/>
      <rect x="314" y="224" width="5" height="34" fill="var(--brand-blue)"/>
      <rect x="324" y="219" width="5" height="44" fill="var(--brand-blue)"/>
      <path d="M304 258 h12 l5 22 h-10 z"/>
    </g>
    <g class="sound-waves" fill="none" stroke="var(--on-brand)" stroke-width="5" stroke-linecap="round">
      <path d="M353 230 q8 11 0 22"/>
      <path d="M363 222 q14 19 0 38"/>
      <path d="M373 214 q20 27 0 54"/>
    </g>
  </svg>

  <div class="status-bar">
    <div class="carrier">
      <svg width="58" height="12" viewBox="0 0 58 12" aria-hidden="true">
        <g fill="var(--on-brand)"><circle cx="6" cy="6" r="5"/><circle cx="18" cy="6" r="5"/><circle cx="30" cy="6" r="5"/></g>
        <g fill="none" stroke="var(--on-brand)" stroke-width="1.5"><circle cx="42" cy="6" r="4.5"/><circle cx="53" cy="6" r="4.5"/></g>
      </svg>
      <span>KESTREL</span>
      <svg width="24" height="18" viewBox="0 0 24 18" aria-hidden="true">
        <g fill="none" stroke="var(--on-brand)" stroke-width="2.5" stroke-linecap="round">
          <path d="M2 6 q10 -9 20 0"/><path d="M6 10 q6 -5 12 0"/>
        </g>
        <circle cx="12" cy="15" r="2.5" fill="var(--on-brand)"/>
      </svg>
    </div>
    <div class="time">4:21 PM</div>
    <div class="system">
      <svg width="12" height="20" viewBox="0 0 12 20" aria-hidden="true">
        <path d="M1 5 l10 10 l-5 4 v-18 l5 4 l-10 10" fill="none" stroke="var(--on-brand)" stroke-width="1.8"/>
      </svg>
      <span>100%</span>
      <svg width="48" height="20" viewBox="0 0 48 20" aria-hidden="true">
        <rect x="1" y="1" width="42" height="18" rx="3" fill="none" stroke="var(--on-brand)" stroke-width="2"/>
        <rect x="4" y="4" width="36" height="12" rx="1" fill="var(--on-brand)"/>
        <rect x="44" y="7" width="3" height="6" fill="var(--on-brand)"/>
      </svg>
    </div>
  </div>

  <h1 class="screen-title">Notifications</h1>

  <section class="intro">
    <p>By enabling push notifications, you can<br>keep up to date with occasional<br>notifications related to items you care<br>about. Select the categories on the<br>next screen and then authorize the<br>push notifications.</p>
    <p>If you ever change your mind, you can<br>adjust these options in the Settings<br>menu of this app.</p>
  </section>

  <div class="next-button" role="button">
    <span>NEXT</span>
    <svg width="26" height="18" viewBox="0 0 26 18" aria-hidden="true">
      <path d="M1 9 H24 M16 2 L24 9 L16 16" fill="none" stroke="var(--on-brand)" stroke-width="2"/>
    </svg>
  </div>
</main>
</body>
</html>
```